Business Card Re-Design/Update

We'd like to update out business cards. I've included our current "Style guide" which has the colour scheme of the organisation in it. I've also included the branding files with logos etc in them.

I've also included a copy of one of our existing cards so that you can see how ugly/dated they look. I'd like a fresh modern corporate look.

Target Market(s)

These are for our clients, potential clients, industry contacts - like all business cards

Contact Information for Business Card

Name
Position
Company Address - Level 1, 47 Fernby Street, Carlow Qld 4072
Direct Phone
mobile
Email
Website -www.korvalit.com.au
Logo

Colors

Designer to choose colors to be used in the design.

Requirements
Must have
• Main Logo
• Cards will need to be editable to be able to personalize them for each new employee.
Nice to have
• The MapOut, ShipWell, KeepSteady would be okay to have if they can be sensibly and professionally added to the look without detracting from the main imagery.
• Maybe they could go on the back of the card? will leave this to your creative discretion as to whether/where they fit.
Should not have
• Should not have decorative or script fonts

```html
<!DOCTYPE html>
<html lang="en">
<head>
<meta charset="utf-8">
<title>korvalIT business card</title>
<link rel="stylesheet" href="https://fonts.googleapis.com/css2?family=Roboto+Condensed:wght@400;500;700&display=swap">
<style>
  :root {
    --page-bg: #e6e6e6;
    --card-white: #f6f6f6;
    --brand-red: #c0141c;
    --brand-red-dark: #8e0a10;
    --brand-red-light: #d8222a;
    --ink: #232323;
    --on-red: #ffffff;
    --back-light: #f2f2f2;
    --back-mid: #dcdcdc;
    --mapout-green: #5c9e3a;
    --shipwell-blue: #2a80c4;
    --keepsteady-magenta: #b3227f;
  }
  * { margin: 0; padding: 0; box-sizing: border-box; }
  html, body { width: 1200px; height: 960px; overflow: hidden; }
  body {
    background: var(--page-bg);
    font-family: "Roboto Condensed", Arial, sans-serif;
    position: relative;
  }
  .card {
    position: absolute;
    width: 600px;
    height: 343px;
    overflow: hidden;
    box-shadow: 0 2px 4px rgba(0,0,0,0.35);
  }
  .card-front { left: 314px; top: 113px; background: var(--card-white); }
  .card-back {
    left: 311px; top: 472px;
    background: linear-gradient(135deg, var(--back-light) 0%, var(--back-mid) 45%, var(--back-light) 70%, var(--back-mid) 100%);
  }
  .red-field { position: absolute; inset: 0; }

  .wordmark {
    position: absolute;
    left: 36px; top: 166px;
    display: flex; align-items: center; gap: 14px;
  }
  .wordmark-square { width: 36px; height: 36px; background: var(--brand-red); }
  .wordmark-name { font-size: 32px; font-weight: 500; color: var(--ink); letter-spacing: 0.2px; }

  .contact {
    position: absolute;
    right: 36px; top: 46px;
    text-align: right;
    color: var(--on-red);
  }
  .person-name { font-size: 21px; font-weight: 700; line-height: 26px; }
  .person-role { font-size: 15px; line-height: 18px; }
  .address { margin-top: 52px; font-size: 15px; line-height: 18px; }
  .lines { margin-top: 9px; list-style: none; }
  .lines li {
    font-size: 14.5px; line-height: 18.4px;
    display: flex; justify-content: flex-end; align-items: center; gap: 9px;
  }
  .lines svg { width: 13px; height: 13px; fill: var(--on-red); flex: none; }

  .back-mark {
    position: absolute;
    left: 240px; top: 68px;
    width: 120px; height: 120px;
    background: var(--brand-red);
  }
  .services {
    position: absolute;
    left: 0; right: 0; top: 276px;
    display: flex; justify-content: center; gap: 34px;
  }
  .service { display: flex; align-items: center; gap: 8px; font-size: 25px; font-weight: 500; }
  .service-square { width: 24px; height: 24px; }
  .service-mapout { color: var(--mapout-green); }
  .service-mapout .service-square { background: var(--mapout-green); }
  .service-shipwell { color: var(--shipwell-blue); }
  .service-shipwell .service-square { background: var(--shipwell-blue); }
  .service-keepsteady { color: var(--keepsteady-magenta); }
  .service-keepsteady .service-square { background: var(--keepsteady-magenta); }
</style>
</head>
<body>

<section class="card card-front">
  <svg class="red-field" viewBox="0 0 600 343" role="img" aria-label="Red panel with layered diamond pattern">
    <defs>
      <linearGradient id="redGrad" x1="0" y1="0" x2="1" y2="1">
        <stop offset="0" stop-color="var(--brand-red-light)"/>
        <stop offset="0.55" stop-color="var(--brand-red)"/>
        <stop offset="1" stop-color="var(--brand-red-dark)"/>
      </linearGradient>
    </defs>
    <polygon points="164,0 600,0 600,343 184,343 356,140 340,124 322,146" fill="url(#redGrad)"/>
  </svg>

  <div class="wordmark">
    <span class="wordmark-square"></span>
    <span class="wordmark-name">korvalIT</span>
  </div>

  <div class="contact">
    <p class="person-name">DANA WHITFIELD</p>
    <p class="person-role">Business Development Manager</p>
    <p class="address">22/15 Marlow Ridge Road<br>Kessington QLD 4011</p>
    <ul class="lines">
      <li>+61 (0)7 3840 5120 <svg viewBox="0 0 16 16"><path d="M3 1l3 0 1 4-2 1.5a9 9 0 0 0 4.5 4.5L11 9l4 1v3c0 1-1 2-2 2A12 12 0 0 1 1 3c0-1 1-2 2-2z"/></svg></li>
      <li>+61 (0)7 3840 5127 <svg viewBox="0 0 16 16"><path d="M3 1l3 0 1 4-2 1.5a9 9 0 0 0 4.5 4.5L11 9l4 1v3c0 1-1 2-2 2A12 12 0 0 1 1 3c0-1 1-2 2-2z"/></svg></li>
      <li>+61 (0)412 604 318 <svg viewBox="0 0 16 16"><path d="M4 0h8a1 1 0 0 1 1 1v14a1 1 0 0 1-1 1H4a1 1 0 0 1-1-1V1a1 1 0 0 1 1-1zm1 2v10h6V2zm3 11a1 1 0 1 0 0 2 1 1 0 0 0 0-2z"/></svg></li>
      <li>+61 (0)7 3840 5199 <svg viewBox="0 0 16 16"><path d="M4 1h8v4H4zM1 6h14v7h-2v-3H3v3H1zM4 11h8v4H4z"/></svg></li>
      <li>dwhitfield@korvalit.com.au <svg viewBox="0 0 16 16"><path d="M1 3h14v10H1zm1.5 1.2L8 8.5l5.5-4.3z"/></svg></li>
      <li>www.korvalit.com.au <svg viewBox="0 0 16 16"><circle cx="8" cy="8" r="7"/></svg></li>
    </ul>
  </div>
</section>

<section class="card card-back" role="img" aria-label="Light grey layered diamond pattern background">
  <div class="back-mark"></div>
  <div class="services">
    <span class="service service-mapout"><span class="service-square"></span>MapOut</span>
    <span class="service service-shipwell"><span class="service-square"></span>ShipWell</span>
    <span class="service service-keepsteady"><span class="service-square"></span>KeepSteady</span>
  </div>
</section>

</body>
</html>
```